Zielgruppe
Die Velorin Akademie bietet Kurse, Seminare & Coachings im Bereich der Kommunikation / Persönlichkeitsentwicklung an.
Folgendes Angebot besteht zur Zeit:
Seminare:
- 'Erste Schritte im Dialog', eine Einführung in die Kommunikation.
- 'Heitere Töchter, ruhige Väter' zum Thema Erziehung.
- 'Reifen mit Gelassenheit', zum Thema Älter werden und den Umgang damit.
Kurse:
- 'Gewaltfreie Kommunikation', Übungsgruppe
Coaching:
- Einzelsitzungen mit Hypnose
Ps: im Anhang unter 'Angabot_Vorlage.pdf' finden Sie mehr Infos zu den einezlenen Angebote.
Aufgabenstellung
Bitte berücksichtigen Sie, dass bereits ein Logo besteht (siehe Anhang).
Vom gesamteindruck her sollte die Website aufgeräumt, übersichtlich, harmonisch, freundlich & frisch wirken.
Es wäre super, wenn die Website authentisch wirkt (und weniger '0815 Business Website').
Bitte bedenken Sie, dass die Website sich an Private richtet, die sich nach einem 'strahlenderen & unbeschwerterem Lebene sehnen'.
Wir haben bereits viele Persönlichkeiten stärken können und möchten dies auch witerhin mit viel Herzblut machen.

```html
<!DOCTYPE html>
<html lang="de">
<head>
<meta charset="utf-8">
<title>Velorin Akademie – Kontakt</title>
<link rel="stylesheet" href="https://fonts.googleapis.com/css2?family=Montserrat:wght@400;500;600&family=Raleway:wght@600;700&display=swap">
<style>
:root{
  --canvas:#eee7e1;
  --white:#ffffff;
  --ink:#2b2b2b;
  --heading:#5b4f6a;
  --muted:#8a8a8a;
  --line:#a9a9a9;
  --accent:#f47347;
  --band:#f0bb88;
  --footer-bar:#9b8876;
  --footer-text:#5a5a5a;
}
*{box-sizing:border-box;margin:0;padding:0}
html,body{width:775px;height:1200px;overflow:hidden;background:var(--canvas);font-family:'Montserrat',sans-serif;color:var(--ink)}
.page{position:absolute;left:86px;top:50px;width:604px;height:1051px;background:var(--white)}

/* hero */
.hero{position:absolute;left:0;top:0;width:604px;height:353px;
  background:radial-gradient(ellipse at 50% 40%,#7f8fc9 0%,#a9b1d6 22%,#d9c0ae 45%,#e6ddd4 65%,#dcdfe6 100%)}
.topbar{position:absolute;left:0;top:0;width:604px;height:38px;background:rgba(248,248,250,.93);display:flex;align-items:center;justify-content:space-between;padding:0 29px 0 16px}
.brand{font-size:8px;font-weight:600;letter-spacing:1px;color:var(--ink);display:flex;align-items:center;gap:5px}
.brand-dot{width:6px;height:6px;border-radius:50%;background:var(--ink)}
.nav{display:flex;gap:18px;align-items:center;font-size:6px;font-weight:500;letter-spacing:.4px}
.nav a{color:var(--ink);text-decoration:none}
.nav .active{color:var(--accent);border:1px solid var(--accent);border-radius:2px;padding:4px 7px;margin:0 -8px 0 -6px}
.hero-title{position:absolute;left:0;width:604px;top:264px;text-align:center;color:#fff;font-size:25px;font-weight:400;letter-spacing:4px;line-height:30px;margin-top:-48px}
.hero-sub{position:absolute;left:0;width:604px;top:254px;text-align:center;color:#fff;font-size:12.5px;font-weight:500;letter-spacing:1px}
.arrow{position:absolute;top:166px}
.arrow.prev{left:12px}.arrow.next{left:576px}
.dots{position:absolute;top:337px;left:288px;display:flex;gap:4px}
.dots span{width:5px;height:5px;border-radius:50%;border:1px solid #fff}
.dots .on{background:#fff}

/* newsletter */
.newsletter{position:absolute;left:0;top:364px;width:604px;height:40px;background:var(--band);display:flex;align-items:center}
.newsletter .label{margin-left:89px;color:#fff;font-size:7px;font-weight:500;letter-spacing:.2px}
.newsletter .field{margin-left:14px;width:213px;height:21px;background:#fff;border:1px solid #c9c2bb;font-size:7px;color:var(--muted);letter-spacing:.8px;padding:6px 7px}
.newsletter .ok{margin-left:9px;width:25px;height:16px;background:var(--accent);color:#fff;font-size:7px;letter-spacing:.8px;display:flex;align-items:center;justify-content:center}

/* contact form */
.contact-title{position:absolute;left:121px;top:447px;font-family:'Raleway',sans-serif;font-weight:700;font-size:17px;letter-spacing:1px;color:var(--heading)}
.input{position:absolute;border:1px solid var(--line);font-size:7px;letter-spacing:.8px;color:var(--muted);padding:6px 10px}
.msg{left:121px;top:493px;width:354px;height:99px;padding:6px 7px}
.name{left:121px;top:610px;width:157px;height:21px}
.firstname{left:316px;top:610px;width:159px;height:21px;padding-left:8px}
.email{left:121px;top:638px;width:354px;height:21px}
.copy{position:absolute;left:122px;top:665px;display:flex;align-items:center;gap:5px;font-size:7px;letter-spacing:.6px;color:var(--muted)}
.copy .box{width:17px;height:17px;border:1px solid var(--line)}
.send{position:absolute;left:121px;top:712px;width:72px;height:17px;background:var(--accent);color:#fff;font-size:7px;letter-spacing:1px;display:flex;align-items:center;justify-content:center}

/* landscape */
.landscape{position:absolute;left:0;top:757px;width:606px;height:169px;
  background:linear-gradient(180deg,#b9bcc6 0%,#d8d4d0 45%,#a99e93 68%,#5d5650 85%,#3b3734 100%)}

/* footer */
.footer-brand{position:absolute;left:156px;top:1053px;font-size:9px;font-weight:500;letter-spacing:1.5px;color:var(--ink);display:flex;align-items:center;gap:6px}
.footer-brand .mark{width:7px;height:7px;border-radius:50%;background:var(--ink)}
.company{position:absolute;left:310px;top:1020px;font-size:8.5px;font-weight:600;letter-spacing:.6px;color:var(--footer-text)}
.address{position:absolute;left:318px;width:104px;top:1040px;font-size:9px;line-height:11px;color:var(--footer-text);text-align:center}
.contact-data{position:absolute;left:465px;top:1040px;font-size:9px;line-height:11px;color:var(--footer-text)}
.contact-data span{display:inline-block;width:39px}
.bottom-bar{position:absolute;left:84px;top:1101px;width:606px;height:52px;background:var(--footer-bar);color:#fff;font-size:8.5px;letter-spacing:.3px}
.bottom-bar .legal{position:absolute;left:38px;top:21px;display:flex;gap:20px}
.bottom-bar .copyright{position:absolute;left:259px;top:21px}
</style>
</head>
<body>
<main class="page">
  <section class="hero" role="img" aria-label="Foto: Hände halten eine gläserne Weltkugel">
    <header class="topbar">
      <div class="brand"><span class="brand-dot"></span>VELORIN AKADEMIE</div>
      <nav class="nav">
        <a href="#">HOME</a>
        <a href="#">ANGEBOT</a>
        <a href="#" class="active">KONTAKT</a>
        <a href="#">ÜBER UNS</a>
      </nav>
    </header>
    <svg class="arrow prev" width="16" height="28" viewBox="0 0 16 28"><polyline points="14,2 2,14 14,26" fill="none" stroke="#fff" stroke-width="1.3"/></svg>
    <svg class="arrow next" width="16" height="28" viewBox="0 0 16 28"><polyline points="2,2 14,14 2,26" fill="none" stroke="#fff" stroke-width="1.3"/></svg>
    <h1 class="hero-title">VELORIN AKADEMIE</h1>
    <p class="hero-sub">NEUE PERSPECTIVEN • NEUE HORIZONTE</p>
    <div class="dots"><span></span><span></span><span class="on"></span></div>
  </section>

  <section class="newsletter">
    <span class="label">ABONNIEREN SIE UNSEREN NEWSLETTER!</span>
    <div class="field">E-MAIL ADRESSE</div>
    <div class="ok">OK</div>
  </section>

  <h2 class="contact-title">WIR FREUEN UNS ÜBER IHRE ANFRAGE</h2>
  <div class="input msg">NACHRICHT</div>
  <div class="input name">NAME</div>
  <div class="input firstname">VORNAME</div>
  <div class="input email">E-MAIL ADRESSE</div>
  <div class="copy"><span class="box"></span>Kopie an meine E-Mail Adresse senden</div>
  <div class="send">SENDEN</div>

  <section class="landscape" role="img" aria-label="Foto: Person sitzt auf einem Felsvorsprung über einem Bergtal im Gegenlicht"></section>
</main>

<footer>
  <div class="footer-brand"><span class="mark"></span>VELORIN AKADEMIE</div>
  <div class="company">VELORIN AKADEMIE GMBH.</div>
  <div class="address">Lindenweg 24<br>4512 Talwiesen</div>
  <div class="contact-data"><span>TEL:</span>0176 482 905<br><span>E-MAIL:</span>info@velorinakademie.ch</div>
  <div class="bottom-bar">
    <div class="legal"><span>Datenschutz</span><span>Impressum</span></div>
    <div class="copyright">VELORIN AKADEMIE | 2019</div>
  </div>
</footer>
</body>
</html>
```